Brivolt Technologies business card design

We need a business card designed with our new logo. it would be great if the card could communicate it is a technology based company.

Target Market(s)

system integrators

Industry/Entity Type

technology, IOT

Contact Information for Business Card

Name, designation, Address, telephone number, email address

Requirements
Must have
• logo and company name
Nice to have
• something to do with technology

```html
<!DOCTYPE html>
<html lang="en">
<head>
<meta charset="UTF-8">
<title>Brivolt Technologies – Business Card</title>
<link rel="stylesheet" href="https://fonts.googleapis.com/css2?family=Exo+2:wght@400;600;700&display=swap">
<style>
  :root {
    --bg-dark: #161616;
    --bg-light: #3a3a3a;
    --card-white: #ffffff;
    --card-dark: #3b3b3d;
    --ink: #38383a;
    --orange: #f7931e;
    --muted: #d6d6d6;
  }
  * { box-sizing: border-box; margin: 0; padding: 0; }
  html, body { width: 1200px; height: 1200px; overflow: hidden; }
  body {
    background: linear-gradient(135deg, var(--bg-dark) 0%, #222 50%, var(--bg-light) 100%);
    font-family: "Exo 2", sans-serif;
    position: relative;
  }
  .card {
    position: absolute;
    width: 720px;
    height: 410px;
    border-radius: 22px;
    overflow: hidden;
    box-shadow: 0 30px 60px rgba(0,0,0,0.55);
  }

  /* Front */
  .card-front {
    left: 110px; top: 130px;
    background: var(--card-white);
  }
  .card-front .pattern {
    position: absolute; inset: 0;
    background: linear-gradient(180deg, #fff6ec 0%, #ffffff 35%, #ffffff 65%, #fff6ec 100%);
  }
  .front-brand {
    position: absolute;
    left: 0; right: 0; top: 0; bottom: 0;
    display: flex; align-items: center; justify-content: center; gap: 22px;
  }
  .brand-square {
    width: 54px; height: 54px; background: var(--orange);
  }
  .brand-name {
    color: var(--ink);
    font-weight: 700;
    font-size: 50px;
    letter-spacing: 1px;
    text-transform: uppercase;
    line-height: 1;
  }

  /* Back */
  .card-back {
    left: 370px; top: 650px;
    background: var(--card-dark);
  }
  .card-back svg { position: absolute; inset: 0; }
  .person {
    position: absolute; left: 56px; top: 170px;
  }
  .person-name {
    color: var(--orange);
    font-weight: 700;
    font-size: 36px;
    letter-spacing: 1px;
    text-transform: uppercase;
    line-height: 1.05;
  }
  .person-title {
    color: var(--muted);
    font-size: 19px;
    margin-top: 4px;
  }
  .contact-list {
    list-style: none;
    margin-top: 26px;
    color: var(--muted);
    font-size: 16px;
    letter-spacing: 0.5px;
  }
  .contact-list li {
    display: flex; align-items: center; gap: 12px;
    margin-bottom: 9px;
  }
  .contact-list svg { position: static; width: 15px; height: 15px; fill: var(--orange); flex: none; }
  .back-brand {
    position: absolute; left: 478px; top: 150px; width: 220px;
    display: flex; align-items: center; gap: 14px;
  }
  .back-brand .brand-square { width: 34px; height: 34px; }
  .back-brand .brand-name { font-size: 25px; line-height: 1.15; }
</style>
</head>
<body>

  <section class="card card-front">
    <div class="pattern" role="img" aria-label="Faint orange circuit-line pattern"></div>
    <div class="front-brand">
      <span class="brand-square"></span>
      <span class="brand-name">Brivolt Technologies</span>
    </div>
  </section>

  <section class="card card-back">
    <svg viewBox="0 0 720 410" width="720" height="410">
      <rect class="pattern-area" width="720" height="410" fill="#3b3b3d" role="img" aria-label="Faint grey circuit-line pattern"/>
      <polyline points="454,0 440,260 596,410" fill="none" stroke="#f7931e" stroke-width="6"/>
      <polygon points="470,0 720,0 720,410 620,410 456,258" fill="#ffffff"/>
    </svg>

    <div class="person">
      <h1 class="person-name">Daniel Reyes</h1>
      <p class="person-title">Founder &amp; CEO</p>
      <ul class="contact-list">
        <li>
          <svg viewBox="0 0 24 24"><path d="M6.6 10.8a15.1 15.1 0 0 0 6.6 6.6l2.2-2.2a1 1 0 0 1 1-.25 11.4 11.4 0 0 0 3.6.57 1 1 0 0 1 1 1V20a1 1 0 0 1-1 1A17 17 0 0 1 3 4a1 1 0 0 1 1-1h3.5a1 1 0 0 1 1 1c0 1.25.2 2.45.57 3.57a1 1 0 0 1-.25 1z"/></svg>
          (555) 318-2046
        </li>
        <li>
          <svg viewBox="0 0 24 24"><path d="M2 5h20v14H2zm2 2v.5l8 5 8-5V7zm0 2.8V17h16V9.8l-8 5z"/></svg>
          dr@brivolttechnologies.com
        </li>
        <li>
          <svg viewBox="0 0 24 24"><circle cx="12" cy="12" r="10"/></svg>
          brivolttechnologies.com
        </li>
      </ul>
    </div>

    <div class="back-brand">
      <span class="brand-square"></span>
      <span class="brand-name">Brivolt<br>Technologies</span>
    </div>
  </section>

</body>
</html>
```